Wine Shop Banners

Banner graphic/images required
Require banner images to match the present online wine shop.

www.korbel-tafelhaus.de

The wine-shop presently has a very clean, simple design, lots of white space, which is very much the trend at the moment.

Requirements
Images or graphic design for present banners visible on the homepage

The colour and feeling of the banners must fit in with the present clean, simple design.

Work required
3 large slide-card/banners (can be more) and 3 smaller fixed banners below. Please view website to see present position of banners.

LARGE BANNERS x 3

Something special with white background within the banner space
White background on each slide-card. Small individual graphic image in the middle of the slide card. This could be either a simple element of wine:
ingredients, fruit (grape), bottle, cork, old bottle label etc. just displaying one item on each slide-card. Preferably with high quality graphic features.

Note:
We are trying the steer away from the classic stereotype wineshop design. The image/s should have a higher, individual graphic touch, which gives the design something different. Sometimes such artistic work is displayed in steampunk or even in nostalgic design, which leaves the viewer slightly memorized with the content.
To clarify: we are not looking for a full steampunk design but possibly certain elements of this will give you an idea what we mean. That is to say, the design can go slightly in this direction without going over the top. Something small but very eye-catching.

SMALLER BANNERS x 3

One idea is:
Showing a symbol e.g. - discount sign "%" against a white background but again with a high graphic quality.

Target Market(s)

People interested in purchasing wine.
Ages approx. 25 to 65

Industry/Entity Type

Shop

Requirements
Must have
• Something special with white background
• Small individual graphic image in the middle of the slide card.
Nice to have
• The image/s should have a higher, individual graphic touch, which gives the design something different. Something that leaves the viewer slightly memorized with the content.
Should not have
• Not the typical classical design that is often seen on wine shops.

```html
<!DOCTYPE html>
<html lang="en">
<head>
<meta charset="utf-8">
<title>Royal Quality Wine Banner</title>
<link href="https://fonts.googleapis.com/css2?family=Cinzel&family=Libre+Baskerville:wght@400;700&family=Arimo&display=swap" rel="stylesheet">
<style>
  :root {
    --page-bg: #ffffff;
    --banner-bg: #fefefe;
    --banner-edge: #ececec;
    --title-green: #2d6a14;
    --title-green-dark: #163f08;
    --tagline-red: #8a0d0d;
    --gift-gold: #a89400;
    --badge-fill: #fbe0b0;
    --badge-shadow: #8a8a8a;
    --badge-text: #4a4a4a;
    --wine-light: #f0e070;
    --wine-deep: #9c8a18;
  }
  html, body {
    margin: 0;
    padding: 0;
    width: 1200px;
    height: 900px;
    overflow: hidden;
    background: var(--page-bg);
  }
  .canvas {
    position: relative;
    width: 1200px;
    height: 900px;
  }
  .banner {
    position: absolute;
    left: 27px;
    top: 180px;
    width: 1140px;
    height: 449px;
    background: radial-gradient(ellipse at 45% 50%, var(--banner-bg) 70%, var(--banner-edge) 100%);
    overflow: hidden;
  }
  .banner-title {
    position: absolute;
    left: 72px;
    top: 76px;
    margin: 0;
    font-family: "Cinzel", serif;
    font-weight: 400;
    font-size: 66px;
    letter-spacing: -1px;
    line-height: 1;
    background: linear-gradient(to bottom, var(--title-green) 0%, var(--title-green-dark) 100%);
    -webkit-background-clip: text;
    background-clip: text;
    color: transparent;
  }
  .banner-tagline {
    position: absolute;
    left: 73px;
    top: 198px;
    margin: 0;
    font-family: "Libre Baskerville", serif;
    font-size: 20px;
    color: var(--tagline-red);
  }
  .banner-gift {
    position: absolute;
    left: 72px;
    top: 278px;
    margin: 0;
    font-family: "Arimo", sans-serif;
    font-size: 38px;
    line-height: 44px;
    color: var(--gift-gold);
  }
  .discount-badge {
    position: absolute;
    left: 790px;
    top: -14px;
    width: 160px;
    height: 160px;
  }
  .discount-text {
    font-family: "Libre Baskerville", serif;
    font-weight: 700;
    fill: var(--badge-text);
  }
  .wine-photo {
    position: absolute;
    left: 750px;
    top: 95px;
    width: 390px;
    height: 354px;
    background: radial-gradient(ellipse at 70% 40%, var(--wine-light) 0%, var(--wine-deep) 45%, rgba(255,255,255,0) 72%);
    opacity: 0.75;
  }
</style>
</head>
<body>
<main class="canvas">
  <section class="banner">
    <h1 class="banner-title">ROYAL QUALITY WINE</h1>
    <p class="banner-tagline">Lorem ipsum dolor sit amet, consectetur adipisicing eiat nulla</p>
    <p class="banner-gift">surprise of wine Gifts for<br>Someone Special</p>
    <div class="wine-photo" role="img" aria-label="Photo of white wine being poured from a bottle into a glass"></div>
    <svg class="discount-badge" viewBox="0 0 160 160" aria-label="15% off">
      <circle cx="84" cy="84" r="76" fill="var(--badge-shadow)" opacity="0.7"/>
      <circle cx="80" cy="80" r="76" fill="var(--badge-fill)"/>
      <text class="discount-text" x="80" y="70" text-anchor="middle" font-size="46">15%</text>
      <text class="discount-text" x="80" y="118" text-anchor="middle" font-size="40">OFF</text>
    </svg>
  </section>
</main>
</body>
</html>
```